Coastal Learner Bureau business cards

Australian company about to start offering its services. We recruit international students to come to study English, vocational education and postgraduate courses in Australia. We help them find the institution and select the right city they want to come to Australia. We are a young, online oriented and supportive agency. Our clients are between 18 and 35 years old, mainly University students, young professionals or people with work experience. We provide much more information that any other agency offer. We administrate a Facebook group with more than 11.000 members that daily ask questions about general information when coming to Australia, while they are here and even after they leave the country

Target Market(s)

International students from South America, Central America and Europe

Industry/Entity Type

Student

Contact Information for Business Card

Tomas Bilbrea
Managing Director
tomas@kelvarin.com.au
www.kelvoria.com.au
+61 491058264
Melbourne, Australia

Font styles to use
Serif
Sans Serif

Colors

Designer to choose colors to be used in the design.

Requirements
Must have
• Horizontal design
• Standard business card size and shape. If font uses green or yellow colours, they will have to match the ones from the logo
Nice to have
• UPDATE: Use the contents of the green image to design one of the card sides. Use our logo in the background of that side as watermark.
• Passport image, or immigration stamps. A picture of the Yarra River (from Melbourne) would be cool as well.
Should not have
• Non-standard business card size and shape
• Not black as the background colour of any sides as we are not a VIP agency or a hight class service. We are orientes to young people and they like colours, pictures, something attractive.
• Vertical design
• NO YELLOW or BLACK AS THE BACKGROUND COLOUR OF ANY SIDE OF THE BIZ CARD

```html
<!DOCTYPE html>
<html lang="en">
<head>
<meta charset="utf-8">
<title>Coastal Learner Bureau business cards</title>
<link rel="stylesheet" href="https://fonts.googleapis.com/css2?family=Jost:wght@400;500;600;700&display=swap">
<style>
  :root {
    --green: #0f6443;
    --yellow: #e8b923;
    --white: #ffffff;
    --ink: #3a3a3a;
    --backdrop: #cbcbcb;
  }
  * { margin: 0; padding: 0; box-sizing: border-box; }
  html, body {
    width: 1200px; height: 1000px; overflow: hidden;
    background: var(--backdrop);
    font-family: "Jost", "Futura", sans-serif;
  }
  .canvas { position: relative; width: 1200px; height: 1000px; }
  .card {
    position: absolute; left: 295px; width: 587px; height: 335px; overflow: hidden;
  }
  .card--front { top: 149px; background: var(--white); }
  .card--back { top: 517px; background: var(--green); }

  .brand {
    position: absolute; display: flex; align-items: center; gap: 10px;
    font-weight: 600; letter-spacing: 0.5px; line-height: 1;
  }
  .brand__dot { width: 14px; height: 14px; border-radius: 50%; background: var(--yellow); flex: none; }
  .card--front .brand { left: 68px; top: 158px; font-size: 44px; color: var(--green); }
  .card--back .brand { left: 0; right: 0; justify-content: center; top: 146px; font-size: 56px; color: var(--white); }

  .divider {
    position: absolute; left: 293px; top: 103px; width: 2px; height: 138px; background: var(--green);
  }
  .contact { position: absolute; left: 314px; top: 99px; }
  .contact__name {
    font-size: 22px; font-weight: 700; color: var(--green); letter-spacing: 1px; line-height: 1.1;
  }
  .contact__role { font-size: 15px; color: var(--ink); letter-spacing: 0.4px; margin-top: 2px; }
  .contact__list { list-style: none; margin-top: 22px; }
  .contact__item {
    display: flex; align-items: center; gap: 10px;
    font-size: 13.5px; color: var(--ink); letter-spacing: 0.6px; height: 19px;
  }
  .contact__item svg { width: 11px; height: 11px; fill: var(--green); flex: none; }

  .front-band { position: absolute; left: 0; bottom: 0; width: 587px; height: 25px; }

  .tagline {
    position: absolute; left: 0; right: 0; top: 290px; text-align: center;
    font-size: 13.5px; font-weight: 500; color: var(--white); letter-spacing: 0.6px;
  }
</style>
</head>
<body>
<main class="canvas">
  <section class="card card--front" aria-label="Business card front">
    <div class="brand"><span class="brand__dot"></span>Kelvoria</div>
    <div class="divider"></div>
    <div class="contact">
      <p class="contact__name">TOMAS BILBREA</p>
      <p class="contact__role">Managing Director</p>
      <ul class="contact__list">
        <li class="contact__item">
          <svg viewBox="0 0 12 12" aria-hidden="true"><path d="M3 0h6a1 1 0 0 1 1 1v10a1 1 0 0 1-1 1H3a1 1 0 0 1-1-1V1a1 1 0 0 1 1-1zm.5 1.5v8h5v-8zM6 10.2a.6.6 0 1 0 0 1.2.6.6 0 0 0 0-1.2z"/></svg>
          +61 491058264
        </li>
        <li class="contact__item">
          <svg viewBox="0 0 12 12" aria-hidden="true"><path d="M0 2.5h12v1L6 7 0 3.5zM0 4.8l6 3.5 6-3.5V10H0z"/></svg>
          tomas@kelvarin.com.au
        </li>
        <li class="contact__item">
          <svg viewBox="0 0 12 12" aria-hidden="true"><path d="M5 0a5 5 0 0 1 4 8l3 3-1 1-3-3A5 5 0 1 1 5 0zm0 2a3 3 0 1 0 0 6 3 3 0 0 0 0-6z"/></svg>
          www.kelvoria.com.au
        </li>
        <li class="contact__item">
          <svg viewBox="0 0 12 12" aria-hidden="true"><path d="M6 0a4.2 4.2 0 0 1 4.2 4.2C10.2 7.4 6 12 6 12S1.8 7.4 1.8 4.2A4.2 4.2 0 0 1 6 0zm0 2.6a1.6 1.6 0 1 0 0 3.2 1.6 1.6 0 0 0 0-3.2z"/></svg>
          Melbourne, Australia
        </li>
      </ul>
    </div>
    <svg class="front-band" viewBox="0 0 587 25" preserveAspectRatio="none" aria-hidden="true">
      <path d="M0 14 Q293.5 -6 587 14 L587 25 L0 25 Z" fill="var(--green)"/>
      <path d="M0 12 Q293.5 -8 587 12" fill="none" stroke="var(--yellow)" stroke-width="1.6"/>
    </svg>
  </section>

  <section class="card card--back" aria-label="Business card back">
    <div class="brand"><span class="brand__dot"></span>Kelvoria</div>
    <p class="tagline">Hacemos más por ti!</p>
  </section>
</main>
</body>
</html>
```